One piece Trade show banner, 8' x 8' square

One piece banner for trade show
8' x 8' airborne geophysical company

Target Market(s)

Business

Industry/Entity Type

mineral exploration and science

Colors
0054AA
0677BA
7BADD7
CADEEF
E8F1F8
FFC000
F8CF3A
FAE287
FDF2CF
FEFAEE

Requirements
Must have
• Company logo (attached), slogan (Airborne Geophysics for Discovery). We are looking for a new banner, for a standard 8 x 8' square one-piece booth. I have attached some pictures, our logo, our old banner for reference, and two examples from unrelated companies from a tradeshow that we like. If its possible I'd like to change the color of the helicopter from green to dark grey. IE, keep the orange and white, just change green to dark grey. Looking for a simple, clean design with minimal text.
Nice to have
• I have attached examples of banners that we like (2xIMG), plus our old 3-piece banner r.
Should not have
• Green in the helicopter. Please change the color of the helicopter with green/orange/white to dark grey/orange/white. IE change the green to dark grey and leave the orange and white alone. I've attached lots of pictures but I don't expect them all to be used.

```html
<!DOCTYPE html>
<html lang="en">
<head>
<meta charset="utf-8">
<title>Skyline GeoScan – Trade Show Banner</title>
<link rel="stylesheet" href="https://fonts.googleapis.com/css2?family=Poppins:wght@400;500;700;800&display=swap">
<style>
  :root {
    --navy: #1a3e8c;
    --panel-blue: #1b4693;
    --panel-blue-light: #22539f;
    --sky-deep: #0a3f9a;
    --sky-mid: #1a6fb5;
    --haze: #5f8fb5;
    --sea: #3d6f9c;
    --rock-dark: #4a3a32;
    --rock: #7a6152;
    --rock-light: #a08672;
    --heli-grey: #56636e;
    --gold: #ffc000;
    --white: #ffffff;
    --url-navy: #1b3a7a;
  }
  * { margin: 0; padding: 0; box-sizing: border-box; }
  html, body { width: 1152px; height: 1200px; overflow: hidden; }
  body {
    background: var(--white);
    font-family: "Poppins", sans-serif;
  }
  .banner {
    position: relative;
    width: 1152px;
    height: 1200px;
    background: var(--white);
    overflow: hidden;
  }

  /* Hero photograph area */
  .hero-photo {
    position: absolute;
    left: 0; top: 0;
    width: 1152px; height: 752px;
    background:
      radial-gradient(ellipse 380px 90px at 480px 215px, rgba(86,99,110,0.55), rgba(86,99,110,0) 100%),
      radial-gradient(ellipse 120px 70px at 330px 180px, rgba(240,140,40,0.25), rgba(240,140,40,0) 100%),
      radial-gradient(ellipse 520px 260px at 900px 620px, rgba(160,134,114,0.55), rgba(160,134,114,0) 100%),
      radial-gradient(ellipse 600px 200px at 200px 460px, rgba(61,111,156,0.8), rgba(61,111,156,0) 100%),
      radial-gradient(ellipse 500px 90px at 850px 330px, rgba(200,215,230,0.35), rgba(200,215,230,0) 100%),
      linear-gradient(180deg,
        var(--sky-deep) 0%,
        var(--sky-mid) 25%,
        var(--haze) 40%,
        #56708a 50%,
        var(--rock) 65%,
        var(--rock-dark) 85%,
        #3e2f28 100%);
  }

  .brand {
    position: absolute;
    right: 82px; top: 30px;
    display: flex; align-items: center; gap: 12px;
    color: var(--white);
    font-weight: 500;
    font-size: 50px;
    letter-spacing: -0.5px;
  }
  .brand-dot {
    width: 16px; height: 16px; border-radius: 50%;
    background: var(--gold);
  }

  .headline {
    position: absolute;
    left: 0; width: 100%;
    top: 408px;
    text-align: center;
    color: var(--white);
    font-weight: 800;
    font-size: 206px;
    line-height: 1;
    letter-spacing: -3px;
    text-shadow: 0 4px 18px rgba(0,0,0,0.18);
  }
  .slogan {
    position: absolute;
    left: 0; width: 100%;
    top: 630px;
    text-align: center;
    color: var(--white);
    font-weight: 800;
    font-size: 72px;
    line-height: 1;
    letter-spacing: -1.8px;
    text-shadow: 0 3px 12px rgba(0,0,0,0.2);
  }

  /* Lower service band */
  .service-photo {
    position: absolute;
    left: 42px; top: 752px;
    width: 318px; height: 380px;
    background:
      radial-gradient(ellipse 60px 30px at 200px 50px, rgba(200,225,255,0.45), rgba(200,225,255,0) 100%),
      radial-gradient(ellipse 110px 70px at 100px 270px, rgba(180,160,150,0.28), rgba(180,160,150,0) 100%),
      linear-gradient(180deg, #0a62d6 0%, #0a4fbe 40%, #0b3a95 75%, #0b2a72 100%);
  }
  .services {
    position: absolute;
    left: 360px; top: 752px;
    width: 698px; height: 380px;
    background: linear-gradient(90deg, var(--panel-blue), var(--panel-blue-light));
    display: grid;
    grid-template-columns: 310px 330px;
    padding: 54px 0 0 52px;
  }
  .service-group { margin-bottom: 30px; }
  .service-title {
    color: var(--gold);
    font-weight: 800;
    font-size: 25px;
    line-height: 1.15;
    margin-bottom: 2px;
    letter-spacing: -0.3px;
  }
  .service-list { list-style: none; }
  .service-list li {
    color: var(--white);
    font-size: 24px;
    line-height: 1.2;
    padding-left: 16px;
    position: relative;
  }
  .service-list li::before {
    content: "•";
    position: absolute; left: 0;
    font-size: 18px;
  }

  .web-address {
    position: absolute;
    left: 0; width: 100%;
    top: 1140px;
    text-align: center;
    color: var(--url-navy);
    font-weight: 800;
    font-size: 37px;
    letter-spacing: 0.3px;
  }
</style>
</head>
<body>
  <main class="banner">
    <div class="hero-photo" role="img" aria-label="Dark grey and orange survey helicopter with long sensor booms flying over rugged coastal cliffs, sea and low cloud under a deep blue sky"></div>

    <div class="brand"><span class="brand-dot"></span>Skyline GeoScan</div>

    <h1 class="headline">AIRBORNE</h1>
    <p class="slogan">GEOPHYSICS FOR DISCOVERY</p>

    <div class="service-photo" role="img" aria-label="Helicopter towing a suspended electromagnetic loop sensor against a deep blue sky"></div>

    <section class="services">
      <div class="service-column">
        <div class="service-group">
          <h2 class="service-title">ELECTROMAGNETICS</h2>
          <ul class="service-list">
            <li>Time domain</li>
            <li>Passive</li>
            <li>VLF-EM</li>
          </ul>
        </div>
        <div class="service-group">
          <h2 class="service-title">RADIOMETRICS</h2>
          <ul class="service-list">
            <li>256/512 channels</li>
            <li>Up to 42 litres</li>
          </ul>
        </div>
      </div>
      <div class="service-column">
        <div class="service-group">
          <h2 class="service-title">MAGNETICS</h2>
          <ul class="service-list">
            <li>Helicopter, fixed wing,<br>and drone</li>
            <li>Total field &amp; gradient</li>
          </ul>
        </div>
        <div class="service-group">
          <h2 class="service-title">CONSULTING</h2>
          <ul class="service-list">
            <li>Survey design</li>
            <li>Interpretations</li>
            <li>Inversions</li>
          </ul>
        </div>
      </div>
    </section>

    <p class="web-address">WWW.SKYLINEGEOSCAN.COM</p>
  </main>
</body>
</html>
```